​Silver Harbor Rhythm provides personal, friendly service in a fun and high energy environment. We are based in Vermont.

We would like a card that appeals to a wide range of audiences as we do a wide range of events. Please feel free to check out our website silverharborrhythm.net for inspiration.

Target Market(s)

weddings, corporate, birthday parties, colleges

Industry/Entity Type

Business

Contact Information for Business Card

Silver Harbor Rhythm
Providing Entertainment For All Occasions
555 274 9160
silverharborrhythm@mailnest.net
silverharborrhythm.net

```html
<!DOCTYPE html>
<html lang="en">
<head>
<meta charset="utf-8">
<title>Silver Harbor Rhythm — Business Card</title>
<link rel="stylesheet" href="https://fonts.googleapis.com/css2?family=Open+Sans:wght@400;600;700&display=swap">
<style>
  :root {
    --page-bg: #ecebe7;
    --card-white: #ffffff;
    --brand-green: #2f5f1f;
    --brand-green-dark: #1f4713;
    --text-dark: #3a3a3a;
    --text-muted: #666666;
    --divider: #c9c9c9;
  }
  * { margin: 0; padding: 0; box-sizing: border-box; }
  html, body {
    width: 1200px; height: 1200px; overflow: hidden;
    background: var(--page-bg);
    font-family: "Open Sans", Arial, sans-serif;
  }
  .canvas { position: relative; width: 1200px; height: 1200px; }
  .card {
    position: absolute; left: 140px; width: 920px; height: 520px;
    border-radius: 28px; overflow: hidden;
    box-shadow: 0 6px 18px rgba(0,0,0,0.18);
  }
  .card--front { top: 50px; background: var(--card-white); }
  .card--back { top: 630px; background: var(--brand-green); }

  .front__brand {
    position: absolute; left: 40px; top: 170px; width: 340px;
    display: flex; align-items: center; gap: 14px;
    color: var(--brand-green); font-weight: 700; font-size: 30px; line-height: 1.15;
  }
  .brand-square { flex: none; width: 26px; height: 26px; background: var(--brand-green); }
  .front__divider {
    position: absolute; left: 400px; top: 36px; width: 2px; height: 300px;
    background: var(--divider);
  }
  .front__details { position: absolute; left: 428px; top: 36px; color: var(--text-dark); }
  .person-name { font-size: 30px; font-weight: 700; color: var(--brand-green); }
  .person-title { font-size: 22px; margin-top: 2px; color: var(--text-dark); }
  .contact-list { list-style: none; margin-top: 22px; }
  .contact-list li {
    display: flex; align-items: center; gap: 10px;
    font-size: 21px; height: 38px; color: var(--text-dark);
  }
  .contact-icon { flex: none; width: 18px; height: 18px; }
  .address { margin-top: 18px; font-size: 21px; line-height: 38px; color: var(--text-muted); }

  .front__swoosh { position: absolute; left: 0; top: 0; width: 920px; height: 520px; }

  .back__brand {
    position: absolute; left: 0; right: 0; top: 150px;
    display: flex; justify-content: center; align-items: center; gap: 20px;
    color: var(--card-white); font-weight: 700; font-size: 54px;
  }
  .back__brand .brand-square { width: 40px; height: 40px; background: var(--card-white); }
  .back__url {
    position: absolute; left: 0; right: 0; bottom: 70px; text-align: center;
    color: var(--card-white); font-size: 26px; font-weight: 600; letter-spacing: 2px;
  }
</style>
</head>
<body>
<main class="canvas">

  <section class="card card--front" aria-label="Business card front">
    <svg class="front__swoosh" viewBox="0 0 920 520" aria-hidden="true">
      <path d="M0 440 C 300 420, 650 410, 920 362 L920 520 L0 520 Z" fill="var(--brand-green)"/>
      <path d="M0 458 C 320 440, 660 428, 920 386 L920 520 L0 520 Z" fill="var(--card-white)"/>
      <path d="M0 472 C 330 456, 680 444, 920 400 L920 520 L0 520 Z" fill="var(--brand-green-dark)"/>
      <path d="M320 472 C 560 462, 760 444, 920 414" fill="none" stroke="var(--card-white)" stroke-width="2"/>
    </svg>

    <div class="front__brand">
      <span class="brand-square"></span>
      <span class="brand-name">Silver Harbor Rhythm</span>
    </div>

    <div class="front__divider"></div>

    <div class="front__details">
      <p class="person-name">Your Name</p>
      <p class="person-title">Title</p>
      <ul class="contact-list">
        <li>
          <svg class="contact-icon" viewBox="0 0 18 18" aria-hidden="true">
            <circle cx="9" cy="9" r="9" fill="var(--brand-green)"/>
            <path d="M6 4.5 L7.8 6.5 L6.9 7.6 C7.5 9 8.9 10.5 10.4 11.1 L11.5 10.2 L13.5 12 L12.3 13.4 C9 13 5 9 4.6 5.7 Z" fill="#fff"/>
          </svg>
          <span>555 274 9160</span>
        </li>
        <li>
          <svg class="contact-icon" viewBox="0 0 18 18" aria-hidden="true">
            <circle cx="9" cy="9" r="9" fill="var(--brand-green)"/>
            <rect x="4.5" y="6" width="9" height="6.5" fill="#fff"/>
            <path d="M4.5 6 L9 9.6 L13.5 6" fill="none" stroke="var(--brand-green)" stroke-width="1"/>
          </svg>
          <span>silverharborrhythm@mailnest.net</span>
        </li>
        <li>
          <svg class="contact-icon" viewBox="0 0 18 18" aria-hidden="true">
            <circle cx="9" cy="9" r="9" fill="var(--brand-green)"/>
            <circle cx="9" cy="9" r="4.5" fill="none" stroke="#fff" stroke-width="1.3"/>
            <path d="M4.5 9 H13.5 M9 4.5 V13.5" stroke="#fff" stroke-width="1"/>
          </svg>
          <span>www.silverharborrhythm.net</span>
        </li>
      </ul>
      <p class="address">Sreet Name, City Name<br>Zip Code-00000</p>
    </div>
  </section>

  <section class="card card--back" aria-label="Business card back">
    <div class="back__brand">
      <span class="brand-square"></span>
      <span class="brand-name">Silver Harbor Rhythm</span>
    </div>
    <p class="back__url">www.silverharborrhythm.net</p>
  </section>

</main>
</body>
</html>
```